Logo and Card design for KRV Home Solutions LLC

I need an edgier logo and business card designs. Current logo attached. I like the colors below. I would like the logo to incorporate a home in the design.
Title = Principal-Acquisitions
Email:KRVHOMESOLUTIONS@fernmail.example
555-214-0937
facebook
IG
2 sided business card with the front being contact info a slogan about selling a home fast. The back incorporating What we do. Buy houses, land, or commercial property as is. We find solutions to make the process of selling simple and fair.

Target Market(s)

Motivated house sellers.

Industry/Entity Type

Business

Contact Information for Business Card

Who we are: We are a Faith based Real Estate Investment Company. We pay cash for homes in any condition and can close quick. Whatever the reason you need to sell fast, we can help. We believe in creating win-win solutions to help you in your time of need. We care! We can help!

Logo Text

KRV Home Solutions LLC

Font styles to use
Sans Serif

Colors
33a6d7
0355a3
85abd2
cee9f5
9d9d9d
b2b2b2
ffffff

Requirements
Must have
• Old logo attached. I want something edgier.
• Company name, phone number, description on the back of what we can do. Pay all cash. Buy in as is condition. No fees,Commisions or closing costs.Close quick. No hassles with solutions to meet your unique situation.
• Call today for an offer within 24 hours.

```html
<!DOCTYPE html>
<html lang="en">
<head>
<meta charset="utf-8">
<title>KRV Home Solutions LLC – Business Card</title>
<link href="https://fonts.googleapis.com/css2?family=Lato:wght@400;700&display=swap" rel="stylesheet">
<style>
  :root {
    --stage: #1e1e1e;
    --navy: #1f3a70;
    --card-front: #f1f1f1;
    --card-back: #ffffff;
    --ink: #2b2b2b;
    --rule: #9d9d9d;
  }
  html, body {
    margin: 0;
    padding: 0;
    width: 1200px;
    height: 900px;
    overflow: hidden;
    background: var(--stage);
    font-family: "Lato", Arial, sans-serif;
  }
  .stage {
    position: relative;
    width: 1200px;
    height: 900px;
  }
  .card {
    position: absolute;
    top: 306px;
    width: 440px;
    height: 271px;
    border-radius: 12px;
    overflow: hidden;
  }
  .card--front { left: 149px; background: var(--card-front); }
  .card--back { left: 608px; background: var(--card-back); }

  .brand {
    display: flex;
    align-items: center;
    gap: 8px;
    margin: 0;
    font-weight: 400;
    white-space: nowrap;
  }
  .brand__mark {
    flex: none;
    width: 12px;
    height: 12px;
  }
  .brand--front {
    position: absolute;
    right: 24px;
    top: 112px;
    color: var(--navy);
    font-size: 19px;
  }
  .brand--front .brand__mark { background: var(--navy); }

  .person { position: absolute; left: 23px; top: 161px; }
  .person__name {
    margin: 0;
    color: var(--navy);
    font-weight: 700;
    font-size: 16px;
    letter-spacing: 0.3px;
  }
  .person__title {
    margin: 1px 0 0;
    color: var(--ink);
    font-size: 12.5px;
  }
  .divider {
    position: absolute;
    left: 23px;
    top: 202px;
    width: 393px;
    height: 1px;
    background: var(--rule);
  }
  .contact {
    position: absolute;
    left: 23px;
    top: 213px;
    margin: 0;
    padding: 0;
    list-style: none;
    color: var(--ink);
    font-size: 13px;
    line-height: 16.5px;
  }
  .contact li { display: flex; align-items: center; gap: 4px; }
  .contact svg { width: 11px; height: 11px; fill: var(--navy); }
  .social {
    position: absolute;
    right: 23px;
    top: 222px;
    display: flex;
    gap: 10px;
  }
  .social span {
    width: 22px;
    height: 22px;
    border-radius: 50%;
    background: var(--navy);
  }

  .back-header {
    position: absolute;
    left: 0; top: 0;
    width: 100%;
    height: 117px;
    background: var(--navy);
    display: flex;
    align-items: center;
    justify-content: center;
  }
  .brand--back {
    color: #fff;
    font-size: 24px;
  }
  .brand--back .brand__mark { background: #fff; }
  .services {
    position: absolute;
    left: 21px;
    top: 150px;
    margin: 0;
    padding: 0;
    list-style: none;
    color: var(--ink);
    font-size: 11.2px;
    line-height: 13.9px;
  }
  .services li { position: relative; padding-left: 9px; }
  .services li::before {
    content: "";
    position: absolute;
    left: 0; top: 5px;
    width: 5px; height: 5px;
    border-radius: 50%;
    background: var(--navy);
  }
</style>
</head>
<body>
<main class="stage">
  <section class="card card--front" aria-label="Card front">
    <h1 class="brand brand--front"><span class="brand__mark" aria-hidden="true"></span>KRV Home Solutions LLC</h1>
    <div class="person">
      <p class="person__name">MARCUS WHITFIELD</p>
      <p class="person__title">Managing Director</p>
    </div>
    <div class="divider"></div>
    <ul class="contact">
      <li><svg viewBox="0 0 24 24" aria-hidden="true"><path d="M6.6 10.8a15 15 0 0 0 6.6 6.6l2.2-2.2a1 1 0 0 1 1-.25 11.4 11.4 0 0 0 3.6.57 1 1 0 0 1 1 1V20a1 1 0 0 1-1 1A17 17 0 0 1 3 4a1 1 0 0 1 1-1h3.5a1 1 0 0 1 1 1c0 1.25.2 2.45.57 3.57a1 1 0 0 1-.25 1z"/></svg>555-214-0937</li>
      <li><svg viewBox="0 0 24 24" aria-hidden="true"><path d="M2 5h20v14H2z M2 5l10 8 10-8" /></svg>KRVHOMESOLUTIONS@fernmail.example</li>
    </ul>
    <div class="social" aria-label="Social profiles">
      <span></span><span></span>
    </div>
  </section>

  <section class="card card--back" aria-label="Card back">
    <header class="back-header">
      <h2 class="brand brand--back"><span class="brand__mark" aria-hidden="true"></span>KRV Home Solutions LLC</h2>
    </header>
    <ul class="services">
      <li>Buy houses, land or commercial property as is.</li>
      <li>Pay all cash.</li>
      <li>Buy in as is condition.</li>
      <li>No fees, commisions or closing costs.</li>
      <li>Close quick. No hassles with solutions to meet</li>
      <li>your unique situation.</li>
      <li>Call today for an offer within 24 hours</li>
    </ul>
  </section>
</main>
</body>
</html>
```